Business cards to launch an education platform

Hi,
I am looking at having new business cards designed.
I am a startup, developing a web platform for schools and university, the education world. It's an online assessment system.
I would like a card that looks classy, and that is using the colors and the font of my logo.

I have attached:
1) my logo
2) A business card that I have designed quickly so you can have all the information required in the card, but I really don't like it.
3) The font that I am using (Lato Regular) to design my web platform
4) Some screenshots of my web platform so you can have a look at the style that I have.

Target Market(s)

Major market: Education system: Schools and university
Minor markets: Business in general

Industry/Entity Type

Business

Contact Information for Business Card

Clara Fenwick
Director

M: 0437 518 902
E: clara.fenwick@amberLoomSystems.com.au

Requirements
Must have
• The colors of my logo

```html
<!DOCTYPE html>
<html lang="en">
<head>
<meta charset="utf-8">
<title>Amber Loom Systems – Business Cards</title>
<link href="https://fonts.googleapis.com/css2?family=Lato:wght@400;700&display=swap" rel="stylesheet">
<style>
  :root{
    --backdrop:#1c1c1e;
    --brand-blue:#1e5bb0;
    --brand-navy:#17418c;
    --sky-light:#1596dd;
    --sky-deep:#0c6fb8;
    --ink:#1b1b1b;
    --muted:#2a2a2a;
    --card-white:#ffffff;
    --card-grey:#e6e6e6;
    --band-grey:#4a4a4a;
    --label-navy:#0d2a4a;
  }
  *{box-sizing:border-box;margin:0;padding:0}
  html,body{width:1200px;height:873px;overflow:hidden}
  body{background:var(--backdrop);font-family:"Lato",sans-serif;position:relative}

  .card{position:absolute;width:560px;height:320px;border-radius:3px;overflow:hidden;
    box-shadow:0 18px 40px rgba(0,0,0,.55)}

  /* back of card */
  .card-back{left:70px;top:110px;
    background:radial-gradient(ellipse at 55% 45%,var(--sky-light) 0%,var(--sky-deep) 75%)}
  .card-back .brand-mark{position:absolute;left:0;right:0;top:118px;text-align:center;
    font-weight:400;font-size:38px;color:#ffffff;letter-spacing:1px}
  .card-back .divider{position:absolute;left:150px;right:40px;top:262px;height:1px;
    background:linear-gradient(90deg,transparent,rgba(255,255,255,.75),transparent)}
  .card-back .tagline{position:absolute;right:44px;top:274px;font-size:13px;
    letter-spacing:4px;color:var(--label-navy)}

  /* front of card */
  .card-front{left:570px;top:450px;
    background:linear-gradient(160deg,var(--card-white) 40%,var(--card-grey) 100%)}
  .logo-lockup{position:absolute;top:52px;left:0;right:0;display:flex;
    justify-content:center;align-items:center;gap:12px}
  .logo-square{width:38px;height:38px;background:var(--brand-blue)}
  .logo-name{font-size:26px;font-weight:400;color:var(--brand-navy);letter-spacing:.5px}

  .holder{position:absolute;right:40px;top:140px;text-align:right}
  .holder-name{font-size:19px;font-weight:700;color:var(--brand-navy)}
  .holder-role{font-size:13px;color:var(--ink);margin-top:2px}

  .icon-rail{position:absolute;left:0;top:178px;width:36px;height:110px;
    background:var(--brand-blue);border-radius:0 10px 10px 0;
    display:flex;flex-direction:column;justify-content:space-around;align-items:center;padding:6px 0}
  .icon-rail svg{width:15px;height:15px;fill:none;stroke:#fff;stroke-width:1.8;
    stroke-linecap:round;stroke-linejoin:round}

  .contact-list{position:absolute;left:52px;top:184px;list-style:none}
  .contact-list li{font-size:13px;font-weight:700;color:var(--muted);height:25px;line-height:25px}

  .band-grey{position:absolute;left:0;right:0;bottom:14px;height:12px;background:var(--band-grey)}
  .band-blue{position:absolute;left:0;bottom:0;width:340px;height:28px;background:var(--brand-blue);
    clip-path:polygon(0 0,calc(100% - 24px) 0,100% 100%,0 100%);
    color:#fff;font-size:13px;letter-spacing:1.5px;line-height:28px;padding-left:64px}
</style>
</head>
<body>

<section class="card card-back" aria-label="Card back">
  <div class="brand-mark">Amber Loom Systems</div>
  <div class="divider"></div>
  <div class="tagline">ONLINE ASSESSMENT SYSTEM</div>
</section>

<section class="card card-front" aria-label="Card front">
  <div class="logo-lockup">
    <span class="logo-square"></span>
    <span class="logo-name">Amber Loom Systems</span>
  </div>

  <div class="holder">
    <div class="holder-name">Clara Fenwick</div>
    <div class="holder-role">Director</div>
  </div>

  <div class="icon-rail">
    <svg viewBox="0 0 16 16" aria-label="Phone"><rect x="4" y="1.5" width="8" height="13" rx="1.5"/><line x1="7" y1="12" x2="9" y2="12"/></svg>
    <svg viewBox="0 0 16 16" aria-label="Email"><rect x="1.5" y="3.5" width="13" height="9" rx="1"/><polyline points="1.5,3.5 8,9 14.5,3.5"/></svg>
    <svg viewBox="0 0 16 16" aria-label="Website"><path d="M6.5 9.5l3-3"/><path d="M7 4.5l1.5-1.5a2.5 2.5 0 013.5 3.5L10.5 8"/><path d="M9 11.5l-1.5 1.5a2.5 2.5 0 01-3.5-3.5L5.5 8"/></svg>
    <svg viewBox="0 0 16 16" aria-label="Address"><path d="M8 14.5s-4.5-4.5-4.5-8a4.5 4.5 0 019 0c0 3.5-4.5 8-4.5 8z"/><circle cx="8" cy="6.5" r="1.5"/></svg>
  </div>

  <ul class="contact-list">
    <li>0437 518 902</li>
    <li>clara.fenwick@amberLoomSystems.com.au</li>
    <li>www.amberLoomSystems.com.au</li>
    <li>PO Box 218 Glebe NSW 2037 AU</li>
  </ul>

  <div class="band-grey"></div>
  <div class="band-blue">ONLINE ASSESSMENT SYSTEM</div>
</section>

</body>
</html>
```